A website for a Maltese Law Firm

Our law firm needs a website to further its business. The site should have a simple yet effective design. We would need the following sections: About us, Practice Areas, About Malta, Contact. These should be further split as follows:

About us: Our firm, Our values, What others say, Offices

Practice Areas: Crimimal, Citizenship & Residence, Sovereign Patron Pathway, Criminal Defence, Civil Litigation, Arbitration and ADR, Commercial and Corporate, Media Law.

About Malta: just one section.

Contact: Just one section

We would also need a news feed at the front of the site to include latest news regarding our cases.

At the bottom we need a section for our Terms and a Privacy Statement.

Our logo is being attached.

Target Market(s)

All clients looking for legal assistance in Malta

Industry/Entity Type

Legal

Coding

Coded - Design and coding required

Number of Pages Required

1 page

Requirements
Must have
• It must be simple yet striking.

```html
<!DOCTYPE html>
<html lang="en">
<head>
<meta charset="utf-8">
<title>Falzon &amp; Derosa Advocates</title>
<link href="https://fonts.googleapis.com/css2?family=Cinzel:wght@400;600&family=Lato:ital,wght@0,400;0,700;1,400&display=swap" rel="stylesheet">
<style>
:root{
  --ink:#2a2b30;
  --dark:#2c2d33;
  --nav-active:#b9babd;
  --pale:#ececec;
  --white:#ffffff;
  --band:#a9aaad;
  --bottom:#cfcfd1;
  --rule:#8a8b8f;
  --text:#3a3a3a;
  --wood-light:#d9c7a4;
  --wood-mid:#8a6543;
  --wood-dark:#3b2818;
}
*{box-sizing:border-box;margin:0;padding:0}
html,body{width:1200px;height:2723px;overflow:hidden}
body{font-family:"Lato",sans-serif;color:var(--text);background:var(--white);position:relative}
.abs{position:absolute}
section,header,footer,nav{position:absolute;left:0;width:1200px}

/* header */
.site-header{top:0;height:107px;background:var(--white)}
.brand{left:73px;top:24px;font-family:"Cinzel",serif;font-size:32px;font-weight:600;color:var(--ink);letter-spacing:.5px;white-space:nowrap}
.top-contact{left:898px;font-family:"Lato",sans-serif;font-weight:700;font-size:16px;color:var(--ink);display:flex;align-items:center;gap:10px;white-space:nowrap}
.top-contact svg{width:24px;height:24px}

/* nav */
.main-nav{top:107px;height:45px;background:var(--dark)}
.main-nav ul{list-style:none;position:absolute;left:69px;top:0;display:flex;height:45px}
.main-nav li{height:45px;display:flex;align-items:center;justify-content:center;font-family:"Cinzel",serif;font-size:15px;color:var(--white);border-right:1px solid #555860;white-space:nowrap}
.main-nav li.active{background:var(--nav-active);color:var(--ink)}

/* hero */
.hero{top:152px;height:425px;background:linear-gradient(90deg,var(--wood-light) 0%,#c9b38c 35%,var(--wood-mid) 65%,var(--wood-dark) 100%)}
.hero-title{left:69px;top:150px;font-family:"Cinzel",serif;font-size:29px;line-height:35px;color:var(--ink);font-weight:600}
.hero-btn{left:69px;top:238px;width:288px;height:51px;background:var(--dark);color:var(--white);font-family:"Cinzel",serif;font-size:18px;font-weight:600;display:flex;align-items:center;justify-content:center}
.slider-dots{left:69px;top:393px;display:flex;gap:6px}
.slider-dots span{width:22px;height:3px;background:var(--white);opacity:.7}
.slider-dots span:first-child{background:var(--dark);opacity:1}

/* welcome */
.welcome{top:577px;height:454px;background:var(--pale)}
.welcome h1{left:69px;top:62px;font-family:"Cinzel",serif;font-weight:400;font-size:29px;color:var(--ink);white-space:nowrap}
.welcome .lead{left:69px;top:114px;width:680px;font-size:15px;line-height:22px;color:var(--ink)}
.welcome .body{left:69px;top:176px;width:690px;font-size:12.6px;line-height:22px}
.pill-btn{display:flex;align-items:center;height:30px;background:#b3b4b7;border:1px solid #777;border-radius:3px;font-size:12px;color:var(--ink);padding-left:8px;position:absolute}
.pill-btn .go{position:absolute;right:-2px;top:-2px;width:34px;height:34px;border-radius:50%;background:var(--dark);display:flex;align-items:center;justify-content:center}
.eval-form{left:797px;top:62px;width:330px;height:325px;border:2px solid var(--dark);background:var(--pale)}
.eval-form h2{position:absolute;left:18px;top:22px;font-family:"Cinzel",serif;font-weight:400;font-size:23px;color:var(--ink);white-space:nowrap}
.field{position:absolute;left:16px;width:294px;background:var(--white);border:1px solid #c9c9c9;font-size:12px;color:#555;padding:9px 10px}

/* practice */
.practice{top:1031px;height:421px;background:var(--white)}
.section-title{width:1200px;text-align:center;font-family:"Cinzel",serif;font-size:27px;color:var(--ink);font-weight:400}
.area{width:250px;text-align:center}
.area .icon{width:101px;height:101px;border:2px solid var(--dark);margin:0 auto;display:flex;align-items:center;justify-content:center;background:var(--white)}
.area .icon.filled{background:var(--dark)}
.area h3{margin-top:26px;font-family:"Cinzel",serif;font-weight:400;font-size:19px;color:var(--ink);white-space:nowrap}
.area p{margin:6px auto 0;width:200px;font-size:13px;line-height:18px;color:var(--ink)}
.area .more{margin-top:10px;font-size:14px;color:var(--ink)}
.side-arrow{width:18px;height:56px}

/* case studies */
.cases{top:1452px;height:526px;background:var(--pale)}
.case{width:310px}
.case .frame{width:310px;height:164px;border:1px solid #bbb;background:var(--white);padding:7px;position:relative}
.case .photo{width:100%;height:100%}
.case .date{position:absolute;left:14px;top:14px;width:46px;background:var(--white);text-align:center;font-size:14px;line-height:18px}
.case .date b{display:block;background:var(--dark);color:var(--white);font-size:16px;line-height:22px}
.case h4{margin-top:14px;font-size:13px;font-weight:700;color:#111}
.case p{margin-top:8px;font-size:12.5px;line-height:19px;color:var(--ink)}
.case .read{margin-top:10px;font-size:12.5px;color:var(--ink)}

/* testimonials */
.testimonials{top:1978px;height:304px;background:var(--white)}
.client-photo{left:136px;top:122px;width:114px;height:116px;background:linear-gradient(180deg,#e6e8ea,#b9bfc6 60%,#2d3038)}
.quote{left:314px;top:122px;width:762px;font-style:italic;font-size:13px;line-height:21px;color:var(--ink)}
.quote-mark{font-family:"Cinzel",serif;font-size:60px;color:#e0e0e0;line-height:1}
.quote .close-mark{font-family:"Cinzel",serif;font-style:normal;font-size:40px;line-height:0;color:#e0e0e0;vertical-align:-14px;margin-left:4px}
.client-name{left:314px;top:228px;font-family:"Cinzel",serif;font-size:18px;color:var(--ink)}

/* call band */
.call-band{top:2282px;height:128px;background:var(--band)}
.call-band p{position:absolute;left:116px;top:30px;font-family:"Cinzel",serif;font-size:28px;line-height:36px;color:var(--white);font-weight:600;white-space:nowrap}
.call-btn{left:844px;top:39px;width:223px;height:46px;background:var(--dark);border:2px solid var(--white);color:var(--white);font-size:22px;font-weight:700;display:flex;align-items:center;justify-content:center}

/* footer */
.site-footer{top:2410px;height:267px;background:var(--dark);color:var(--white)}
.foot-head{font-family:"Cinzel",serif;font-size:16px;padding-bottom:8px;border-bottom:1px solid #55575e}
.quick-links{left:69px;top:48px;width:140px}
.quick-links ul{margin-top:12px;padding-left:12px;font-size:12px;line-height:24.5px;font-weight:700}
.contact-details{left:301px;top:48px;width:490px}
.map{left:303px;top:86px;width:256px;height:125px;background:linear-gradient(135deg,#eceae2,#d4d9cf);border:1px solid #888}
.contact-list{left:590px;top:90px;font-size:12px;font-weight:700;line-height:16px}
.contact-list div{display:flex;gap:12px;align-items:flex-start;margin-bottom:9px}
.contact-list svg{width:14px;height:14px;flex:none;margin-top:1px}
.foot-brand{left:856px;top:104px;width:300px;text-align:center;font-family:"Cinzel",serif;font-size:15px;font-weight:600;color:var(--white);white-space:nowrap}
.socials{left:924px;top:150px;display:flex;gap:12px}
.socials span{width:32px;height:32px;border-radius:50%;background:#6b6e78;border:1px solid #9a9ca3}
.bottom-bar{top:2677px;height:46px;background:var(--bottom);font-size:12px;color:var(--ink)}
.bottom-bar .copy{left:69px;top:16px}
.bottom-bar .legal{right:73px;top:16px}
</style>
</head>
<body>

<header class="site-header">
  <div class="abs brand">Falzon &amp; Derosa Advocates</div>
  <div class="abs top-contact" style="top:24px">
    <svg viewBox="0 0 24 24"><rect x="1" y="1" width="22" height="22" rx="4" fill="#2c2d33"/><path d="M8 5h3v4H9a8 8 0 0 0 6 6v-2h4v3a2 2 0 0 1-2 2A12 12 0 0 1 6 7a2 2 0 0 1 2-2z" fill="#fff"/></svg>
    555-014-2290
  </div>
  <div class="abs top-contact" style="top:58px">
    <svg viewBox="0 0 24 24"><rect x="1" y="1" width="22" height="22" rx="4" fill="#2c2d33"/><rect x="5" y="7" width="14" height="10" fill="#fff"/><path d="M5 7l7 6 7-6" stroke="#2c2d33" stroke-width="1.5" fill="none"/></svg>
    hello@fdadvocates.example
  </div>
</header>

<nav class="main-nav">
  <ul>
    <li class="active" style="width:91px">Home</li>
    <li style="width:163px">About Malta</li>
    <li style="width:182px">Practice Areas</li>
    <li style="width:125px">Our Firm</li>
    <li style="width:147px">Our Values</li>
    <li style="width:201px">What Others Say</li>
    <li style="width:151px">Contact Us</li>
  </ul>
</nav>

<section class="hero" role="img" aria-label="Wooden judge's gavel resting on its sound block in warm light">
  <h2 class="abs hero-title">Realize Your Constitutional<br>Right For Qualified Legal Help</h2>
  <div class="abs hero-btn">Get A Free Consultation</div>
  <div class="abs slider-dots"><span></span><span></span><span></span></div>
</section>

<section class="welcome">
  <h1 class="abs">Welcome To Falzon &amp; Derosa Advocates</h1>
  <p class="abs lead">Lorem ipsum dolor sit amet, consectetuer adipiscing elit, sed diam nonummy nibh euismod tincidunt ut laoreet dolore magna aliquam erat volutpat.</p>
  <p class="abs body">Lorem ipsum dolor sit amet, consectetur adipiscing elit. Sed vitae magna tellus. Aenean ante nunc, semper nec cursus non, rutrum ac eros. Vestibulum mattis justo ac dui bibendum consequat a ac ipsum. Praesent a arcu venenatis, auctor velit eu, suscipit libero. Quisque convallis, leo ac pharetra sagittis, ipsum arcu auctor urna, sit amet cursus risus augue in eros. Duis lacinia nisi vitae leo commodo, non finibus magna maximus. Sed posuere, neque eget bibendum pulvinar, ligula erat suscipit dolor, ut maximus arcu mi et tortor. Quisque imperdiet turpis et ligula mollis ultricies. Mauris lacinia rhoncus odio, at rutrum diam mollis eu. Quisque ut ipsum faucibus, tristique dui vitae, posuere orci.</p>
  <div class="pill-btn" style="left:69px;top:359px;width:118px">READ MORE
    <span class="go"><svg width="12" height="12" viewBox="0 0 12 12"><path d="M4 2l4 4-4 4" stroke="#fff" stroke-width="2" fill="none"/></svg></span>
  </div>
  <form class="abs eval-form">
    <h2>Free Case Evaluation</h2>
    <div class="field" style="top:80px;height:40px">Name</div>
    <div class="field" style="top:130px;height:40px">Email</div>
    <div class="field" style="top:181px;height:74px">Message</div>
    <div class="pill-btn" style="left:16px;top:269px;width:116px;height:34px;font-size:14px;padding-left:12px">SUBMIT
      <span class="go" style="width:38px;height:38px"><svg width="12" height="12" viewBox="0 0 12 12"><path d="M4 2l4 4-4 4" stroke="#fff" stroke-width="2" fill="none"/></svg></span>
    </div>
  </form>
</section>

<section class="practice">
  <h2 class="abs section-title" style="top:56px">Our Practice Areas</h2>
  <svg class="abs side-arrow" style="left:28px;top:212px" viewBox="0 0 18 56"><path d="M16 2L3 28l13 26" stroke="#555" stroke-width="2" fill="none"/></svg>
  <svg class="abs side-arrow" style="left:1154px;top:212px" viewBox="0 0 18 56"><path d="M2 2l13 26L2 54" stroke="#555" stroke-width="2" fill="none"/></svg>

  <div class="abs area" style="left:75px;top:122px">
    <div class="icon"><svg width="54" height="40" viewBox="0 0 54 40"><circle cx="15" cy="24" r="10" stroke="#2c2d33" stroke-width="5" fill="none"/><circle cx="39" cy="24" r="10" stroke="#2c2d33" stroke-width="5" fill="none"/><path d="M22 10h10" stroke="#2c2d33" stroke-width="5"/></svg></div>
    <h3>Crimimal</h3>
    <p>Lorem ipsum dolor sit amet, consectetuer Lorem dolor sit amet, consectetuer</p>
    <div class="more">[+]</div>
  </div>
  <div class="abs area" style="left:334px;top:122px">
    <div class="icon filled"><svg width="40" height="52" viewBox="0 0 40 52"><rect x="2" y="2" width="36" height="48" rx="3" fill="#fff"/><circle cx="20" cy="22" r="8" stroke="#2c2d33" stroke-width="2" fill="none"/><path d="M12 22h16M20 14v16" stroke="#2c2d33" stroke-width="1.5"/><rect x="12" y="38" width="16" height="3" fill="#2c2d33"/></svg></div>
    <h3>Citizenship &amp; Residence</h3>
    <p>Lorem ipsum dolor sit amet, consectetuer Lorem dolor sit amet, consectetuer</p>
    <div class="more">[+]</div>
  </div>
  <div class="abs area" style="left:605px;top:122px">
    <div class="icon"><svg width="56" height="52" viewBox="0 0 56 52"><circle cx="28" cy="12" r="8" fill="#2c2d33"/><rect x="10" y="22" width="36" height="22" fill="#2c2d33"/><path d="M16 30h24M16 36h24" stroke="#fff" stroke-width="2"/><path d="M2 20h8M46 20h8M2 44h8M46 44h8" stroke="#2c2d33" stroke-width="2"/></svg></div>
    <h3>Criminal Defence</h3>
    <p>Lorem ipsum dolor sit amet, consectetuer Lorem dolor sit amet, consectetuer</p>
    <div class="more">[+]</div>
  </div>
  <div class="abs area" style="left:877px;top:122px">
    <div class="icon"><svg width="52" height="50" viewBox="0 0 52 50"><rect x="14" y="4" width="20" height="14" transform="rotate(45 24 11)" fill="#2c2d33"/><path d="M30 18l16 16" stroke="#2c2d33" stroke-width="5"/><rect x="4" y="42" width="28" height="5" fill="#2c2d33"/></svg></div>
    <h3>Civil Litigation</h3>
    <p>Lorem ipsum dolor sit amet, consectetuer Lorem dolor sit amet, consectetuer</p>
    <div class="more">[+]</div>
  </div>
</section>

<section class="cases">
  <h2 class="abs section-title" style="top:56px">Case Studies</h2>
  <article class="abs case" style="left:69px;top:123px">
    <div class="frame"><div class="photo" role="img" aria-label="Shelves of leather-bound law books" style="background:linear-gradient(90deg,#5a3518,#a8742e,#3e2412,#b98a3c,#4a2b14)"></div><div class="date"><b>06</b>Jun</div></div>
    <h4>Lorem Ipsum Dolor Sit Amet &nbsp;Consectetur</h4>
    <p>Lorem ipsum dolor sit amet, consectetur adipiscing elit. Sed vitae magna tellus. Aenean ante nunc, semper nec cursus non, rutrum ac eros.</p>
    <div class="read">Read More &rsaquo;&rsaquo;</div>
  </article>
  <article class="abs case" style="left:445px;top:123px">
    <div class="frame"><div class="photo" role="img" aria-label="Defendant in handcuffs standing in a courtroom" style="background:linear-gradient(90deg,#4a2618,#8a5a3e,#2c2a2e,#6b4232)"></div><div class="date"><b>06</b>Jun</div></div>
    <h4>Lorem Ipsum Dolor Sit Amet &nbsp;Consectetur</h4>
    <p>Lorem ipsum dolor sit amet, consectetur adipiscing elit. Sed vitae magna tellus. Aenean ante nunc, semper nec cursus non, rutrum ac eros.</p>
    <div class="read">Read More &rsaquo;&rsaquo;</div>
  </article>
  <article class="abs case" style="left:817px;top:123px">
    <div class="frame"><div class="photo" role="img" aria-label="Hands signing a legal document at a desk" style="background:linear-gradient(90deg,#2e2f34,#d9d6d0 55%,#f2f0ec)"></div><div class="date"><b>07</b>Jun</div></div>
    <h4>Lorem Ipsum Dolor Sit Amet &nbsp;Consectetur</h4>
    <p>Lorem ipsum dolor sit amet, consectetur adipiscing elit. Sed vitae magna tellus. Aenean ante nunc, semper nec cursus non, rutrum ac eros.</p>
    <div class="read">Read More &rsaquo;&rsaquo;</div>
  </article>
  <div class="pill-btn" style="left:537px;top:454px;width:120px;height:30px;justify-content:center;padding-left:0;padding-right:30px">VIEW ALL
    <span class="go"><svg width="12" height="12" viewBox="0 0 12 12"><path d="M4 2l4 4-4 4" stroke="#fff" stroke-width="2" fill="none"/></svg></span>
  </div>
</section>

<section class="testimonials">
  <h2 class="abs section-title" style="top:58px">Client Testimonials</h2>
  <svg class="abs side-arrow" style="left:28px;top:146px" viewBox="0 0 18 56"><path d="M16 2L3 28l13 26" stroke="#555" stroke-width="2" fill="none"/></svg>
  <svg class="abs side-arrow" style="left:1154px;top:146px" viewBox="0 0 18 56"><path d="M2 2l13 26L2 54" stroke="#555" stroke-width="2" fill="none"/></svg>
  <div class="abs client-photo" role="img" aria-label="Portrait of a smiling client in a suit"></div>
  <div class="abs quote-mark" style="left:306px;top:100px">&ldquo;</div>
  <p class="abs quote">&nbsp;&nbsp;&nbsp;&nbsp;&nbsp;Lorem ipsum dolor sit amet, consectetuer adipiscing elit, sed diam nonummy nibh euismod tincidunt ut laoreet dolore magna aliquam erat volutpat. Ut wisi enim ad minim veniam, quis nostrud exerci iriure dolor in Lorem ipsum dolor sit amet, consectetuer adipiscing elit, sed diam nonummy nibh euismod tincidunt ut laoreet dolore magna aliquam erat volutpat. Ut wisi enim ad minim veniam, quis nostrud exerci iriure dolo.<span class="close-mark">&rdquo;</span></p>
  <div class="abs client-name">- Daniel Brincat</div>
</section>

<section class="call-band">
  <p>For Any Legal Problem, We Can Help You<br>Anytime take An Appointment Now</p>
  <div class="abs call-btn">CONTACT US</div>
</section>

<footer class="site-footer">
  <div class="abs quick-links">
    <div class="foot-head">QUICK LINKS</div>
    <ul>
      <li>Home</li><li>About Malta</li><li>Practice Areas</li><li>Our Firm</li><li>Our Values</li><li>What Others Say</li><li>Contact Us</li>
    </ul>
  </div>
  <div class="abs contact-details"><div class="foot-head">CONTACT DETAILS</div></div>
  <div class="abs map" role="img" aria-label="Street map showing the office location"></div>
  <div class="abs contact-list">
    <div><svg viewBox="0 0 14 14"><path d="M7 1a4 4 0 0 1 4 4c0 3-4 8-4 8S3 8 3 5a4 4 0 0 1 4-4z" fill="#fff"/><circle cx="7" cy="5" r="1.5" fill="#2c2d33"/></svg><span>Falzon &amp; Derosa Advocates<br>12/7, Harbour Lane, Valletta<br>88, Orchard Street, Birkirkara</span></div>
    <div><svg viewBox="0 0 14 14"><path d="M3 1h3v3H5a6 6 0 0 0 4 4V7h3v3a2 2 0 0 1-2 2A9 9 0 0 1 1 3a2 2 0 0 1 2-2z" fill="#fff"/></svg><span>555-014-229</span></div>
    <div><svg viewBox="0 0 14 14"><rect x="3" y="1" width="8" height="4" fill="#fff"/><rect x="1" y="5" width="12" height="5" fill="#fff"/><rect x="3" y="9" width="8" height="4" fill="#fff" stroke="#2c2d33"/></svg><span>555-014-229</span></div>
    <div><svg viewBox="0 0 14 14"><rect x="1" y="3" width="12" height="8" fill="#fff"/><path d="M1 3l6 5 6-5" stroke="#2c2d33" fill="none"/></svg><span>hello@fdadvocates.example</span></div>
  </div>
  <div class="abs foot-brand">Falzon &amp; Derosa Advocates</div>
  <div class="abs socials"><span></span><span></span><span></span><span></span></div>
</footer>

<div class="abs bottom-bar" style="left:0;width:1200px">
  <div class="abs copy">Copyright &copy; 2016 <b>Falzon &amp; Derosa Advocates</b>. All Rights Reserved.</div>
  <div class="abs legal">Terms &amp; Conditions &nbsp;|&nbsp; Privacy Policy &nbsp;|&nbsp; Disclaimer</div>
</div>

</body>
</html>
```